Wallet/Purse themed website design

We need a simple but visually stunning graphic design for a new web based company called "thecardvaultly.com".

TheCardVaultly is an online/phone app offering extremely secure backup/storage for our users' personal documentation, such as credit cards, ID, passports, certificates, insurance etc.

Documents will be uploaded via a mobile app (initially zPad) to the storage. Retrieval is only possible via login together with bank level authentication (using personal questions).

Our service will not prevent the theft of our customer's physical wallet however our retrieval service can be accessed anywhere online and assist with the replacement. (for example a lost passport will require a new passport request which requires details of the lost passport number/details).
The key audiences for TheCardVaultly include holidaymakers, businessmen, individuals, banking customers

We have specified that the initial design needs only to have 3 pages - home page, login page, wallet contents retrieval page.

Common themes of the following should be strongly brought to bear on the pages:
-Leather wallet/stitching
-Secure/safe/private/encryted
-Personal - for example family holiday
-Access anywhere
-Pick pockets can easily steal your wallet
Updates

Thank you for all of your submissions!  This was our first attempt to source a design via Pixel Bazaar and we will certainly use this resource again.

Thank you.

Target Market(s)

Industry/Entity Type

Graphic Design

Requirements
Must have
• 3 pages - home page, login page, wallet contents retrieval page.
Nice to have
• Modern UI design appealing to families and individuals

```html
<!DOCTYPE html>
<html lang="en">
<head>
<meta charset="utf-8">
<title>TheCardVaultly – Home, Login and Wallet Pages</title>
<link rel="stylesheet" href="https://fonts.googleapis.com/css2?family=Nunito+Sans:wght@400;600;700;800&display=swap">
<style>
  :root {
    --sky-blue: #0a56a6;
    --deep-blue: #003a78;
    --night-blue: #021a36;
    --header-navy: #06366b;
    --panel-orange: #f26722;
    --button-blue: #0652a0;
    --icon-blue: #1f5fa8;
    --field-white: #ffffff;
    --text-white: #ffffff;
    --brand-gold: #f7a21b;
  }
  * { box-sizing: border-box; margin: 0; padding: 0; }
  html, body { width: 1200px; height: 900px; overflow: hidden; }
  body {
    position: relative;
    font-family: "Nunito Sans", Arial, sans-serif;
    color: var(--text-white);
    background:
      linear-gradient(180deg, rgba(2,26,54,0) 0%, rgba(2,26,54,0) 78%, rgba(2,26,54,0.85) 90%, var(--night-blue) 100%),
      radial-gradient(ellipse at 50% 40%, var(--sky-blue) 0%, var(--deep-blue) 100%);
  }
  .floor-shade {
    position: absolute; left: 40px; top: 740px; width: 1160px; height: 160px;
    background: linear-gradient(180deg, rgba(0,25,55,0.55), rgba(0,10,25,0.9));
    transform: skewX(-8deg);
    filter: blur(3px);
  }
  .brand-name {
    position: absolute; left: 0; top: 64px; width: 1200px;
    text-align: center;
    font-size: 76px; font-weight: 800; letter-spacing: 2px; line-height: 1;
    color: var(--brand-gold);
    z-index: 3;
  }
  .site-header {
    position: absolute; left: 70px; top: 111px; width: 1057px; height: 114px;
    background: var(--header-navy);
    box-shadow: 0 8px 18px rgba(0,0,0,0.45);
    z-index: 2;
  }
  .header-label {
    position: absolute; top: 54px;
    font-size: 34px; font-weight: 600; color: var(--text-white);
    display: flex; align-items: center; gap: 12px;
  }
  .header-label svg { display: block; }
  .label-brand { left: 20px; }
  .label-login { left: 383px; }
  .label-home { left: 740px; }

  .panel {
    position: absolute; top: 225px; height: 490px;
    background: var(--panel-orange);
    box-shadow: 6px 10px 18px rgba(0,0,0,0.5);
  }
  .panel-home { left: 79px; width: 339px; }
  .panel-login { left: 436px; width: 328px; }
  .panel-wallet { left: 780px; width: 337px; }

  .photo-slot {
    position: absolute; left: 23px; top: 21px; width: 289px; height: 265px;
    background: radial-gradient(ellipse at 55% 55%, #caa48a 0%, #6b4e3c 28%, #f4f1ee 60%, #ffffff 100%);
  }
  .icon-row { position: absolute; left: 24px; top: 316px; }
  .icon-row svg { position: absolute; top: 0; }
  .footer-links {
    position: absolute; top: 446px; left: 0; width: 100%;
    font-size: 18px; font-weight: 600;
  }
  .footer-links span { position: absolute; }

  .form-row { position: absolute; left: 7px; font-size: 24px; font-weight: 600; }
  .form-field {
    position: absolute; left: 143px; width: 172px; height: 29px;
    background: var(--field-white);
  }
  .action-button {
    position: absolute; height: 30px;
    background: var(--button-blue);
    color: var(--text-white);
    font-size: 23px; font-weight: 600;
    text-align: center; line-height: 30px;
  }
  .submit-button { left: 85px; top: 255px; width: 132px; }
  .device-slot {
    position: absolute; left: 124px; top: 305px; width: 96px; height: 161px;
    border-radius: 8px;
    background: linear-gradient(90deg, #bfc2c4 0%, #f4f4f4 40%, #e2e3e4 70%, #a9acae 100%);
  }

  .detail-label { position: absolute; left: 34px; font-size: 24px; font-weight: 600; }
  .wallet-slot {
    position: absolute; left: 52px; top: 308px; width: 190px; height: 144px;
    transform: rotate(14deg);
    border-radius: 6px;
    background: linear-gradient(160deg, #3a3432 0%, #141110 60%, #6f8a5e 100%);
  }
</style>
</head>
<body>
  <div class="floor-shade"></div>

  <div class="brand-name">thecardvaultly.com</div>

  <header class="site-header">
    <div class="header-label label-brand">Card Vaultly
      <svg width="82" height="52" viewBox="0 0 82 52" aria-hidden="true">
        <g fill="none" stroke="var(--icon-blue)" stroke-width="3">
          <path d="M2 4 H14 L22 36 H70"/>
          <path d="M16 10 H78 L72 30 H21"/>
          <path d="M30 10 V30 M42 10 V30 M54 10 V30 M66 10 V30 M18 20 H75"/>
        </g>
        <circle cx="28" cy="44" r="5" fill="var(--icon-blue)"/>
        <circle cx="64" cy="44" r="5" fill="var(--icon-blue)"/>
      </svg>
    </div>
    <div class="header-label label-login">Secure Login
      <svg width="88" height="44" viewBox="0 0 88 44" aria-hidden="true">
        <ellipse cx="70" cy="22" rx="16" ry="19" fill="var(--icon-blue)"/>
        <circle cx="74" cy="14" r="4" fill="var(--header-navy)"/>
        <path d="M2 18 H56 V27 H36 L32 32 L28 27 L24 32 L20 27 H8 Z" fill="var(--icon-blue)"/>
      </svg>
    </div>
    <div class="header-label label-home">Home Page
      <svg width="62" height="46" viewBox="0 0 62 46" aria-hidden="true">
        <g fill="none" stroke="#ffffff" stroke-width="3">
          <path d="M2 20 L31 3 L60 20 Z"/>
          <rect x="8" y="20" width="46" height="24"/>
          <rect x="14" y="26" width="10" height="18"/>
          <rect x="32" y="26" width="14" height="10"/>
        </g>
      </svg>
    </div>
  </header>

  <section class="panel panel-home">
    <div class="photo-slot" role="img" aria-label="Photo of a couple smiling while using a laptop together"></div>
    <div class="icon-row">
      <svg style="left:0" width="68" height="42" viewBox="0 0 68 42" aria-label="Email">
        <rect x="2" y="2" width="64" height="38" fill="none" stroke="#fff" stroke-width="3"/>
        <path d="M2 2 L34 26 L66 2 M2 40 L26 20 M66 40 L42 20" fill="none" stroke="#fff" stroke-width="3"/>
      </svg>
      <svg style="left:99px" width="54" height="46" viewBox="0 0 54 46" aria-label="Website">
        <g fill="none" stroke="#fff" stroke-width="3">
          <ellipse cx="27" cy="23" rx="25" ry="21"/>
          <ellipse cx="27" cy="23" rx="11" ry="21"/>
          <path d="M2 23 H52 M6 12 H48 M6 34 H48 M27 2 V44"/>
        </g>
      </svg>
      <svg style="left:176px" width="64" height="48" viewBox="0 0 64 48" aria-label="Search">
        <g fill="none" stroke="#fff" stroke-width="3">
          <ellipse cx="22" cy="21" rx="20" ry="18"/>
          <ellipse cx="22" cy="21" rx="9" ry="18"/>
          <path d="M2 21 H42 M5 11 H39 M5 31 H39"/>
          <circle cx="38" cy="30" r="9"/>
        </g>
        <path d="M45 37 L60 46" stroke="#fff" stroke-width="6" stroke-linecap="round"/>
      </svg>
      <svg style="left:252px" width="36" height="44" viewBox="0 0 36 44" aria-label="More">
        <ellipse cx="18" cy="22" rx="16" ry="20" fill="none" stroke="#fff" stroke-width="3"/>
        <path d="M18 12 V32 M8 22 H28" stroke="#fff" stroke-width="4"/>
      </svg>
    </div>
    <nav class="footer-links">
      <span style="left:9px">Contact</span>
      <span style="left:137px">About Us</span>
      <span style="left:276px">Store</span>
    </nav>
  </section>

  <section class="panel panel-login">
    <label class="form-row" style="top:18px">Username</label>
    <div class="form-field" style="top:19px"></div>
    <label class="form-row" style="top:72px">Password</label>
    <div class="form-field" style="top:71px"></div>
    <label class="form-row" style="top:127px">Question</label>
    <div class="form-field" style="top:127px"></div>
    <label class="form-row" style="top:184px">Answers</label>
    <div class="form-field" style="top:184px"></div>
    <div class="action-button submit-button">Submit</div>
    <div class="device-slot" role="img" aria-label="White tablet in a folio case"></div>
  </section>

  <section class="panel panel-wallet">
    <div class="detail-label" style="top:16px">Name</div>
    <div class="detail-label" style="top:70px">Details</div>
    <div class="action-button" style="left:24px; top:127px; width:131px">Back</div>
    <div class="action-button" style="left:179px; top:125px; width:131px">Next</div>
    <div class="action-button" style="left:24px; top:210px; width:131px">Edit</div>
    <div class="action-button" style="left:179px; top:207px; width:131px">Delete</div>
    <div class="wallet-slot" role="img" aria-label="Black leather wallet with banknotes tucked inside"></div>
  </section>
</body>
</html>
```